Bry7Legal Letterhead

Need a new letterhead for my law firm.
IDENTIFYING INFORMATION BELOW:
Anselmo R Quintara III
Attorney at Law
Address: 2847 Larkspur Blvd, Ste 300, Dallas, TX 75204
Phone: 877-482-6017
Fax: 469-738-1452
Email: bry@bry7legal.example
Website: www.bry7legal.example

Colors
0054AA
0677BA
7BADD7
CADEEF
E8F1F8

Requirements
Must have
• Logo needs to be on the letterhead, along with identifying information which is included in the project description.

```html
<!DOCTYPE html>
<html lang="en">
<head>
<meta charset="utf-8">
<title>Bry7Legal Letterhead</title>
<link rel="stylesheet" href="https://fonts.googleapis.com/css2?family=Arimo:wght@400;700&display=swap">
<style>
  :root {
    --backdrop: #e4e4e4;
    --paper: #f2f2f2;
    --ink: #1e1e1e;
    --brand-deep: #0054aa;
    --brand-mid: #0677ba;
    --brand-soft: #7badd7;
    --brand-pale: #8fbde2;
    --rule: #8a8a8a;
    --sign-fill: #e3e6ea;
  }
  * { margin: 0; padding: 0; box-sizing: border-box; }
  html, body { width: 1200px; height: 1200px; overflow: hidden; }
  body {
    background: var(--backdrop);
    font-family: "Arimo", Arial, sans-serif;
    color: var(--ink);
  }
  .letterhead {
    position: absolute;
    left: 180px; top: 6px;
    width: 840px; height: 1188px;
    background: var(--paper);
    box-shadow: 0 6px 24px rgba(0,0,0,.12);
  }
  .brand {
    position: absolute;
    left: 77px; top: 76px;
    display: flex; align-items: center; gap: 10px;
  }
  .brand-mark {
    width: 14px; height: 14px;
    background: var(--brand-deep);
  }
  .brand-name {
    font-size: 30px; font-weight: 400;
    color: var(--ink);
    letter-spacing: 0;
  }
  .sender {
    position: absolute;
    left: 434px; top: 57px;
    font-size: 13.4px; line-height: 17px;
  }
  .sender-name { color: var(--brand-deep); font-weight: 700; }
  .header-divider {
    position: absolute;
    left: 613px; top: 58px;
    width: 1px; height: 66px;
    background: var(--rule);
  }
  .contact-list {
    position: absolute;
    left: 635px; top: 57px;
    list-style: none;
    font-size: 13.4px; line-height: 17px;
  }
  .contact-list li { display: flex; align-items: center; gap: 8px; }
  .contact-list svg { width: 11px; height: 11px; fill: var(--brand-deep); flex: none; }
  .letter {
    position: absolute;
    left: 90px; top: 281px;
    width: 661px;
    font-size: 13.6px; line-height: 19.8px;
  }
  .letter-date { margin-bottom: 20px; }
  .recipient { margin-bottom: 39px; }
  .salutation { margin-bottom: 20px; }
  .body-text { text-align: justify; margin-bottom: 20px; }
  .closing { margin-top: 58px; }
  .signature {
    display: block;
    width: 190px; height: 30px;
    margin-top: 4px;
    background: var(--sign-fill);
    border-radius: 3px;
  }
  .footer-bands {
    position: absolute;
    left: 0; bottom: 0;
    width: 100%; height: 15px;
    display: flex;
  }
  .footer-bands span { flex: 1; }
  .band-deep { background: var(--brand-deep); }
  .band-mid { background: var(--brand-mid); }
  .band-soft { background: var(--brand-soft); }
  .band-pale { background: var(--brand-pale); }
</style>
</head>
<body>
<main class="letterhead">
  <div class="brand">
    <span class="brand-mark"></span>
    <span class="brand-name">Bry7Legal</span>
  </div>

  <div class="sender">
    <div class="sender-name">Anselmo R Quintara III</div>
    <div>Attorney at Law</div>
    <div>2847 Larkspur Blvd</div>
    <div>Ste 300, Dallas, TX 75204</div>
  </div>

  <div class="header-divider"></div>

  <ul class="contact-list">
    <li><svg viewBox="0 0 12 12" aria-hidden="true"><path d="M2.5 1 4.5 1 5.3 3.6 4 4.6c.7 1.5 1.9 2.7 3.4 3.4l1-1.3L11 7.5v2c0 .8-.7 1.5-1.5 1.5C5 11 1 7 1 2.5 1 1.7 1.7 1 2.5 1z"/></svg>877-482-6017</li>
    <li><svg viewBox="0 0 12 12" aria-hidden="true"><path d="M3 1h6v3H3zM1 5h10v5H9V8H3v2H1zM3.5 9h5v2h-5z"/></svg>469-738-1452</li>
    <li><svg viewBox="0 0 12 12" aria-hidden="true"><path d="M1 3h10v6H1zM1.5 3.5 6 7l4.5-3.5" stroke="#f2f2f2" stroke-width="1"/></svg>bry@bry7legal.example</li>
    <li><svg viewBox="0 0 12 12" aria-hidden="true"><path d="M6 1a5 5 0 1 0 0 10A5 5 0 0 0 6 1zm0 1.2c.6.6 1.1 1.7 1.2 2.8H4.8C4.9 3.9 5.4 2.8 6 2.2zM2.3 5h1.4c0 1 .2 1.8.5 2.6A3.8 3.8 0 0 1 2.3 5zm2.5 2C4.9 8.1 5.4 9.2 6 9.8 6.6 9.2 7.1 8.1 7.2 7zm3 .6c.3-.8.5-1.6.5-2.6h1.4a3.8 3.8 0 0 1-1.9 2.6z"/></svg>www.bry7legal.example</li>
  </ul>

  <section class="letter">
    <p class="letter-date">01 January 2050</p>
    <p class="recipient">Company (Pvt) Ltd.<br>PO Box 3355 Mainville St<br>Sample City Country 3355</p>
    <p class="salutation">Dear Dorian Valcourt,</p>
    <p class="body-text">Lorem ipsum dolor sit amet, consectetuer adipiscing elit, sed diam nonummy nibh euismod tincidunt ut laoreet dolore magna aliquam erat volutpat. Ut wisi enim ad minim veniam, quis nostrud exerci tation ullamcorper suscipit lobortis nisl ut aliquip ex ea commodo consequat. Duis dolore te feugait nulla facilisi. Nam liber tempor cum soluta nobis eleifend option congue nihil imperdiet doming id quod mazim placerat facer possim assum. Lorem ipsum dolor sit amet, consectetuer adipiscing elit, sed diam nonummy nibh euismod tincidunt ut laoreet dolore magna aliquam erat volutpat. Ut wisi enim ad minim veniam, quis nostrud exerci tation ullamcorper suscipit lobortis nisl ut aliquip ex ea commodo consequat.</p>
    <p class="body-text">Consectetuer adipiscing elit, sed diam nonummy nibh euismod tincidunt ut laoreet dolore magna aliquam erat volutpat. Ut wisi enim ad minim veniam, quis nostrud exerci tation ullamcorper suscipit lobortis nisl ut aliquip ex ea commodo consequat. Consectetuer adipiscing elit, sed diam nonummy nibh euismod tincidunt ut laoreet dolore magna aliquam erat volutpat. Ut wisi enim ad minim veniam, quis nostrud exerci tation ullamcorper suscipit lobortis nisl ut aliquip ex ea commodo consequat.</p>
    <p class="body-text">Consectetuer adipiscing elit, sed diam nonummy nibh euismod tincidunt ut laoreet dolore magna aliquam erat volutpat. Ut wisi enim ad minim veniam, quis nostrud exerci tation ullamcorper suscipit lobortis nisl ut aliquip ex ea commodo consequat. Consectetuer adipiscing elit, sed diam nonummy nibh euismod tincidunt ut laoreet dolore magna aliquam erat volutpat. Ut wisi enim ad minim veniam, quis nostrud exerci tation ullamcorper suscipit lobortis nisl ut aliquip ex ea commodo consequat.</p>
    <p class="closing">Sincerely Yours</p>
    <span class="signature" role="img" aria-label="Handwritten signature of Marcus Ellwood"></span>
  </section>

  <div class="footer-bands">
    <span class="band-deep"></span>
    <span class="band-mid"></span>
    <span class="band-soft"></span>
    <span class="band-pale"></span>
  </div>
</main>
</body>
</html>
```